Website Design for Forklift Training Company

DO NOT CONTACT PRIVATELY. ONLY SUBMISSIONS HERE WILL BE CONSIDERED

I need a design for a website that offers forklift training courses.

The company offers accredited, onsite forklift training that are customized for the needs of each individual company. The company offers a variety of courses to operate forklifts and other machinary.

About: "KVW Training Ltd delivers bespoke onsite forklift truck operator training throught the uk.
All our instructors have a wealth of knowledge and expertise to provide your company with all your forklift truck training requirements.
KVW Training Ltd is registered and accredited by plomvex standards so you can be rest assured that all forklift training is carried out the very highest standard"

I need the following pages designed:
> a) Home Page: Include a header image, ways to contact, about snippet, overview of courses, accreditation that will be received after completing the courses. (See attachments for samples)
> b) About Page
> c) Contact Us Page
> d) Course Page Template: A page that will be used as template for the courses offered. It should contain;
1. Cover image for the course
2. A description of the course
3. A table indicating the various course options
4. Course Objectives
5. What the trainee will receive after doing the course (example: a certification)

Industrial Businesses

4 page

Colors
0054AA
0677BA
7BADD7
CADEEF
E8F1F8
0094D4
00A9DD
6FCCEA
C7EBF8
E9F6FB

• - No Search bar

```html
<!DOCTYPE html>
<html lang="en">
<head>
<meta charset="utf-8">
<title>KVW Training Ltd – Forklift Training Courses</title>
<link href="https://fonts.googleapis.com/css2?family=Oswald:wght@300;400;500;600&family=Lato:wght@400;700&display=swap" rel="stylesheet">
<style>
:root{
  --blue:#0c47a8;
  --blue-dark:#0a3c8f;
  --blue-band:#0d4aa6;
  --blue-band-2:#1a5cbf;
  --ink:#111;
  --text:#333;
  --orange:#f0a020;
  --pale:#eef4fb;
  --card:#f3f3f3;
  --footer:#1e2735;
  --white:#fff;
}
*{box-sizing:border-box;margin:0;padding:0}
html,body{width:1200px;height:4736px;overflow:hidden}
body{font-family:'Lato',sans-serif;color:var(--text);background:var(--white);position:relative}
h1,h2,h3,h4{font-family:'Oswald',sans-serif;color:var(--ink);text-transform:uppercase;font-weight:500}
section,header,footer{position:absolute;left:0;width:1200px}
.abs{position:absolute}
.btn{position:absolute;display:flex;align-items:center;justify-content:center;background:var(--blue);color:#fff;font-family:'Lato',sans-serif;font-weight:700;text-transform:uppercase;font-size:15px;border-radius:2px}

/* hero */
.hero{top:0;height:653px;background:linear-gradient(100deg,#3a3d40 0%,#5a5548 35%,#7a6a4a 55%,#3d4650 100%)}
.hero .brand{left:95px;top:9px;display:flex;align-items:center;gap:14px}
.brand-mark{width:86px;height:74px;background:#141414}
.brand-name{font-family:'Oswald',sans-serif;font-size:30px;color:#fff;line-height:1;letter-spacing:-.5px;font-weight:500}
.brand-sub{font-family:'Lato',sans-serif;font-size:12px;color:var(--orange);letter-spacing:2.5px;margin-top:4px}
.nav{top:32px;left:577px;font-size:16px;color:#fff;font-weight:700}
.nav span{position:absolute;white-space:nowrap}
.hero h1{left:110px;top:248px;font-size:62px;line-height:58px;color:#fff;font-weight:500}
.arrow{position:absolute;top:300px}
.dots{position:absolute;left:556px;top:606px;display:flex;gap:14px}
.dots i{width:12px;height:12px;border-radius:50%;background:rgba(255,255,255,.5)}
.dots i:first-child{background:#fff}

/* about */
.about{top:653px;height:524px}
.about .photo{left:121px;top:88px;width:456px;height:340px;background:linear-gradient(160deg,#d9dde2,#9aa3ad 60%,#c7b18a)}
.about h2{left:640px;top:98px;font-size:40px;font-weight:500;line-height:1.1}
.about p{left:640px;top:158px;width:430px;font-size:14.5px;line-height:25.7px;text-align:justify;color:#333}

/* courses band */
.courses{top:1177px;height:1070px;background:linear-gradient(135deg,var(--blue-band) 0%,var(--blue-band-2) 50%,var(--blue-band) 100%)}
.courses h2{width:100%;text-align:center;top:90px;font-size:38px;color:#fff;font-weight:500}
.course-card{position:absolute;width:310px;height:390px;background:#fff;text-align:center}
.course-card .img{height:197px;background:linear-gradient(160deg,#8a939c,#c9ccc7 55%,#c47a2e)}
.course-card h3{font-size:23px;margin-top:16px;font-weight:500}
.course-card p{font-size:14px;line-height:25.5px;padding:0 12px;margin-top:6px;color:#444}
.course-card .btn{left:95px;bottom:16px;width:122px;height:34px;font-size:12px;background:var(--blue-dark)}

/* training list */
.training{top:2247px;height:608px}
.training>h2{width:100%;text-align:center;top:80px;font-size:40px;font-weight:500}
.t-card{position:absolute;top:143px;width:312px;height:381px;background:#fff;border:1px solid #eee;box-shadow:0 0 8px rgba(0,0,0,.08);padding:30px 0 0 22px}
.t-card h3{font-size:31px;line-height:34px;font-weight:500}
.t-card ul{list-style:none;margin-top:18px}
.t-card li{font-size:12.5px;line-height:30.8px;display:flex;align-items:center;gap:10px;color:#222}
.t-card li::before{content:"";width:9px;height:9px;border:3px solid var(--orange);border-radius:50%;background:#fff;flex:none}
.t-card .btn{left:20px;top:317px;width:158px;height:46px;font-size:17px;font-weight:400}

/* accreditation */
.accred{top:2855px;height:831px;background:var(--pale)}
.accred h2{width:100%;text-align:center;top:70px;font-size:40px;font-weight:500}
.badge{left:116px;top:151px;width:77px;height:79px;background:#1f2a78;border:3px solid #0f1a55}
.accred .txt{left:112px;width:980px;font-size:13px;line-height:25.7px;color:#222}
.alt-mark{left:112px;top:537px;font-family:'Lato',sans-serif;font-size:40px;font-weight:700;color:#1f3f8f;display:flex;align-items:center;gap:10px}
.alt-mark i{width:22px;height:22px;background:#7cb342}

/* trending */
.trending{top:3686px;height:675px}
.trending>h2{width:100%;text-align:center;top:88px;font-size:40px;font-weight:500}
.post{position:absolute;top:162px;width:314px;height:427px;background:var(--card)}
.post .img{height:210px;background:linear-gradient(160deg,#b9c1c8,#6f7780 55%,#d8a030)}
.date{position:absolute;left:14px;top:180px;width:58px;height:52px;background:var(--orange);color:#fff;text-align:center;font-family:'Oswald',sans-serif;font-size:26px;line-height:34px}
.date small{display:block;font-family:'Lato',sans-serif;font-size:7px;line-height:8px}
.post h3{font-size:29px;line-height:32px;text-transform:none;font-weight:300;margin:30px 14px 0}
.post p{font-size:14px;line-height:25px;margin:8px 14px 0;color:#444}
.post .more{margin:8px 14px 0;font-family:'Oswald',sans-serif;font-size:13px;color:var(--blue);font-weight:500}

/* footer */
footer{top:4361px;height:375px;background:var(--footer);color:#fff}
footer .brand{left:110px;top:93px;display:flex;align-items:center;gap:14px}
footer .brand .brand-mark{width:92px;height:81px;background:#0c0c0c}
.fcol{position:absolute;top:98px;font-size:14px;line-height:27px}
.fcol h4{color:#fff;font-size:19px;font-weight:400;margin-bottom:2px}
.fcol .row{display:flex;gap:8px;align-items:flex-start}
.fcol svg{flex:none;margin-top:6px}
.sep{left:118px;top:290px;width:966px;height:1px;background:#3d4757}
.copy{top:318px;width:100%;text-align:center;font-size:14px}
</style>
</head>
<body>

<header class="hero">
  <div role="img" aria-label="Smiling forklift instructor in hard hat and hi-vis vest standing in front of a row of forklift trucks" style="position:absolute;inset:0"></div>
  <div class="abs brand">
    <div class="brand-mark"></div>
    <div><div class="brand-name">KVW TRAINING LTD</div><div class="brand-sub">Forklift Truck Training</div></div>
  </div>
  <nav class="abs nav">
    <span style="left:0">Home</span>
    <span style="left:94px">Forklift Training Courses
      <svg width="10" height="8" viewBox="0 0 10 8"><path d="M1 2l4 4 4-4" stroke="#fff" stroke-width="1.6" fill="none"/></svg></span>
    <span style="left:351px">About</span>
    <span style="left:447px">Contact</span>
  </nav>
  <h1 class="abs">Forklift Training<br>Courses</h1>
  <div class="btn" style="left:110px;top:388px;width:158px;height:46px;font-size:16px">Get Started</div>
  <svg class="arrow" style="left:66px" width="22" height="44" viewBox="0 0 22 44"><path d="M18 4L4 22l14 18" stroke="#fff" stroke-width="2" fill="none"/></svg>
  <svg class="arrow" style="left:1100px" width="22" height="44" viewBox="0 0 22 44"><path d="M4 4l14 18L4 40" stroke="#fff" stroke-width="2" fill="none"/></svg>
  <div class="dots"><i></i><i></i><i></i><i></i><i></i></div>
</header>

<section class="about">
  <div class="abs photo" role="img" aria-label="Instructor with trainees in hi-vis vests around a pallet truck in a warehouse"></div>
  <h2 class="abs">Forklift Training Courses</h2>
  <p class="abs">We specialise in onsite forklift training using the equipment and facilities your employees will use in there everyday work wether its counterbalance stackwell hoistex cherry picker to name a few. We also accommodate an anytime any shift training schedule to cater for your different shift patterns.By the time we have finished your staff will be well trained and ready to operate efficiently and safely</p>
  <div class="btn" style="left:640px;top:360px;width:158px;height:48px;font-size:15px">Learn More</div>
</section>

<section class="courses">
  <h2 class="abs">Our Courses</h2>
  <div class="course-card" style="left:112px;top:169px"><div class="img" role="img" aria-label="Pallet trucks in a clean warehouse"></div><h3>Finibus Bonorum et Malor</h3><p>Lorem ipsum dolor sit aonsectetur adipiscing elit, sed do ei tempor incididunt ut labore et dolore magna aliqua.</p><div class="btn">Learn More</div></div>
  <div class="course-card" style="left:443px;top:169px"><div class="img" role="img" aria-label="Trainee at forklift controls with instructor"></div><h3>Finibus Bonorum et Malor</h3><p>Lorem ipsum dolor sit aonsectetur adipiscing elit, sed do ei tempor incididunt ut labore et dolore magna aliqua.</p><div class="btn">Learn More</div></div>
  <div class="course-card" style="left:774px;top:169px"><div class="img" role="img" aria-label="Instructor guiding a forklift operator between racking"></div><h3>Finibus Bonorum et Malor</h3><p>Lorem ipsum dolor sit aonsectetur adipiscing elit, sed do ei tempor incididunt ut labore et dolore magna aliqua.</p><div class="btn">Learn More</div></div>
  <div class="course-card" style="left:112px;top:581px"><div class="img" role="img" aria-label="Workers in hard hats checking a clipboard in a warehouse"></div><h3>Finibus Bonorum et Malor</h3><p>Lorem ipsum dolor sit aonsectetur adipiscing elit, sed do ei tempor incididunt ut labore et dolore magna aliqua.</p><div class="btn">Learn More</div></div>
  <div class="course-card" style="left:443px;top:581px"><div class="img" role="img" aria-label="Forklift lifting a pallet of bottled water"></div><h3>Finibus Bonorum et Malor</h3><p>Lorem ipsum dolor sit aonsectetur adipiscing elit, sed do ei tempor incididunt ut labore et dolore magna aliqua.</p><div class="btn">Learn More</div></div>
  <div class="course-card" style="left:774px;top:581px"><div class="img" role="img" aria-label="Forklift loading boxes into a lorry trailer"></div><h3>Finibus Bonorum et Malor</h3><p>Lorem ipsum dolor sit aonsectetur adipiscing elit, sed do ei tempor incididunt ut labore et dolore magna aliqua.</p><div class="btn">Learn More</div></div>
</section>

<section class="training">
  <h2 class="abs">Our Training Courses</h2>
  <div class="t-card" style="left:110px">
    <h3>Forklift Training<br>Courses</h3>
    <ul><li>Arto Truck Training Course</li><li>Multiway Lift Training course</li><li>Counterbalance Training Course</li><li>Veratru Truck Training Course</li><li>Hoistex Crane Training Course</li><li>Llop Training Course</li></ul>
    <div class="btn">Learn More</div>
  </div>
  <div class="t-card" style="left:441px">
    <h3>MEWP Training<br>Courses</h3>
    <ul><li>Cherry Picker Training Course</li><li>Scissor Lift Training Course</li><li>Harness And Lanyard Training Course</li></ul>
    <div class="btn">Learn More</div>
  </div>
  <div class="t-card" style="left:773px">
    <h3>Other Training<br>Courses</h3>
    <ul><li>Bobrig Truck Training Course</li><li>Front Loading Shovel Training Course</li><li>Overhead Pendant Crane Training Course</li><li>Swing Colum Jib Crane Training Course</li><li>Slinging and Signalling Training Course</li><li>Vehicle Banksman Training Course</li></ul>
    <div class="btn">Learn More</div>
  </div>
</section>

<section class="accred">
  <h2 class="abs">Forklift Training Accreditation</h2>
  <div class="abs badge"></div>
  <p class="abs txt" style="top:253px">Plomvex is recognised throughout the united kingdom and Ireland as one of the leading material handling equipment training accrediting bodies.</p>
  <p class="abs txt" style="top:290px">Plomvex is a founder member of the Norvale (accrediting bodies association for workplace transport) and this replaced the accrediting bodies forum previously run by the HSR. They have over 40 years experience of setting training standards,accreditation and monitoring. The Plomvex accreditation schemes are supported by legal requirements for training.The health and safety at work act 1974 prescribes a legal duty to provide adequate training and instruction to their employees.This is reinforced by the provision &amp; use of work equipment regulations of 1998 which states that all persons using work equipment must be trained, including the methods of using equipment, any risks and precautions taken.</p>
  <p class="abs txt" style="top:430px">The Plomvex accreditation schemes and standards are guided by the Approved code of practice for rider operated lift trucks.( ACOP L117). The code has special legal status. If you are prosecuted for a breach off health and safety law, and its proved that you did not follow the relevant provisions of the (ACOP L117) you will need to show that you have complied with the law in some other way or a court will find fault</p>
  <div class="abs alt-mark"><i></i>norvale</div>
  <p class="abs txt" style="top:628px">We are accredited by the Plomvex who are recognised by the national workplace safety authority as competent to deliver forklift truck operator training courses.</p>
  <p class="abs txt" style="top:664px;line-height:25px">As an Plomvex accredited training provider we are monitored annually to ensure we are maintaining our high standards as laid down by the Plomvex.<br>All our instructors are qualified and registered with the Plomvex and monitored.<br>Please note we are only accredited to deliver training at customer premises as we do not have a training centre.</p>
</section>

<section class="trending">
  <h2 class="abs">See What's Trending</h2>
  <div class="post" style="left:112px"><div class="img" role="img" aria-label="Orange forklift loading a curtain-sided lorry"></div><div class="date">29<small>JULY 2021</small></div><h3>The standard Lorem Ipsum passage, used</h3><p>Lorem ipsum dolor sit amet, tur adipiscing elit, sed dood tempor incididunt ut labore et dolore magna aliqua.</p><div class="more">READ MORE »</div></div>
  <div class="post" style="left:443px"><div class="img" role="img" aria-label="Two workers in hard hats reviewing a tablet"></div><div class="date">29<small>JULY 2021</small></div><h3>The standard Lorem Ipsum passage, used</h3><p>Lorem ipsum dolor sit amet, tur adipiscing elit, sed dood tempor incididunt ut labore et dolore magna aliqua.</p><div class="more">READ MORE »</div></div>
  <div class="post" style="left:774px"><div class="img" role="img" aria-label="Forklift driver in hi-vis seated in cab"></div><div class="date">29<small>JULY 2021</small></div><h3>The standard Lorem Ipsum passage, used</h3><p>Lorem ipsum dolor sit amet, tur adipiscing elit, sed dood tempor incididunt ut labore et dolore magna aliqua.</p><div class="more">READ MORE »</div></div>
</section>

<footer>
  <div class="abs brand">
    <div class="brand-mark"></div>
    <div><div class="brand-name">KVW TRAINING LTD</div><div class="brand-sub">Forklift Truck Training</div></div>
  </div>
  <div class="fcol" style="left:454px">
    <h4>CONTACT US</h4>
    <div class="row"><svg width="12" height="16" viewBox="0 0 12 16"><path d="M6 1a5 5 0 0 0-5 5c0 4 5 9 5 9s5-5 5-9a5 5 0 0 0-5-5z" fill="#fff"/><circle cx="6" cy="6" r="2" fill="#1e2735"/></svg><span>14 Fenmore Lane, Ashcombe,<br>Dunridge, DR4 7QX</span></div>
    <div class="row" style="margin-top:8px"><svg width="14" height="14" viewBox="0 0 14 14"><path d="M3 1l2.5 3-1.5 1.5c.8 1.8 2.2 3.2 4 4L9.5 8 13 10.5 11.5 13C6 13 1 8 1 2.5z" fill="#fff"/></svg><span>07000 123456</span></div>
    <div class="row" style="margin-top:8px"><svg width="16" height="12" viewBox="0 0 16 12"><rect x="1" y="1" width="14" height="10" fill="#fff"/><path d="M1 1l7 6 7-6" stroke="#1e2735" fill="none"/></svg><span>info@kvwtraining.example</span></div>
  </div>
  <div class="fcol" style="left:733px">
    <h4>BUSINESS HOURS</h4>
    <div>Mon - FriOpen 24 Hours</div>
    <div>Saturday6:00 - 18:00</div>
    <div>SundayAppointment Only</div>
  </div>
  <div class="fcol" style="left:967px">
    <h4>LET'S CONNECT</h4>
    <div>Facepage</div>
    <div>Chirper</div>
    <div>Circles</div>
  </div>
  <div class="abs sep"></div>
  <div class="abs copy">© 2021 All Rights Reserved | KVW Training Ltd</div>
</footer>

</body>
</html>
```